We need a logo design that explain all the products we possess.
The main goal is to represent graphically all the logos, pointing to one single logo - Vellamor.
The descriptions are in french.
I have uploaded a file with 4 logos to use:
Vellamor (the logo that all the rest should be pointing to)
RTN
Ombrevik
TroupéLune
All logo must be used in the vector graphic format, the description file is in each folder, it's the description that should be next to the logo.

The main goal of this is to create a banner 10' x 11' (estimated)

Target Market(s)

Cities

Requirements
Must have
• All the logos in the zip file in vector graphic.
Nice to have
• A background
Should not have
• Do not use KOL logo, it's a mix with RTN, and Kol Blue/dark blue with inscription "RTN", Charging fees for a part of the picture is not ok!

```html
<!DOCTYPE html>
<html lang="fr">
<head>
<meta charset="utf-8">
<title>Vellamor — Portail et services</title>
<link rel="stylesheet" href="https://fonts.googleapis.com/css2?family=Montserrat:wght@500;700;800&display=swap">
<style>
  :root {
    --bg-deep: #3f6db3;
    --bg-light: #5b8fd4;
    --panel: #ffffff;
    --frame: #8f9194;
    --ink-label: #5a5a5c;
    --brand-blue: #3d6fbd;
    --sky-blue: #5aa4e0;
    --navy: #2c4a8c;
  }
  * { margin: 0; padding: 0; box-sizing: border-box; }
  html, body { width: 1200px; height: 1091px; overflow: hidden; }
  body {
    position: relative;
    font-family: "Montserrat", sans-serif;
    background: radial-gradient(ellipse 60% 55% at 50% 55%, var(--bg-light), var(--bg-deep) 80%);
  }
  .pyramid { position: absolute; inset: 0; }
  .brand {
    position: absolute;
    transform: translateX(-50%);
    display: flex;
    flex-direction: column;
    align-items: center;
    white-space: nowrap;
  }
  .brand-name { font-weight: 800; line-height: 1; }
  .brand-label {
    font-size: 13.5px;
    font-weight: 700;
    line-height: 1;
    letter-spacing: 0.03em;
    color: var(--ink-label);
  }

  .brand--rtn { left: 600px; top: 240px; }
  .brand--rtn .brand-mark { width: 84px; height: 110px; background: var(--brand-blue); border-radius: 4px; }
  .brand--rtn .brand-name { margin-top: 12px; font-size: 32px; font-weight: 700; color: var(--brand-blue); letter-spacing: 0.02em; }
  .brand--rtn .brand-label { margin-top: 14px; }

  .brand--vellamor { left: 600px; top: 605px; }
  .brand--vellamor .brand-mark { width: 70px; height: 70px; border-radius: 50%; background: var(--brand-blue); }
  .brand--vellamor .brand-name { margin-top: 28px; font-size: 40px; color: var(--brand-blue); letter-spacing: 0.02em; }
  .brand--vellamor .brand-label { margin-top: 10px; }

  .brand--troupelune { left: 320px; top: 772px; }
  .brand--troupelune .brand-mark { width: 80px; height: 80px; border-radius: 50%; background: var(--sky-blue); }
  .brand--troupelune .brand-name { margin-top: 40px; font-size: 30px; color: var(--sky-blue); }
  .brand--troupelune .brand-label { margin-top: 18px; }

  .brand--ombrevik { left: 853px; top: 800px; }
  .brand--ombrevik .brand-mark { width: 80px; height: 80px; background: var(--navy); }
  .brand--ombrevik .brand-name { margin-top: 20px; font-size: 24px; font-weight: 500; color: var(--navy); letter-spacing: 0.16em; }
  .brand--ombrevik .brand-label { margin-top: 14px; }
</style>
</head>
<body>
  <svg class="pyramid" width="1200" height="1091" viewBox="0 0 1200 1091" aria-hidden="true">
    <defs>
      <filter id="lift" x="-10%" y="-10%" width="120%" height="120%">
        <feDropShadow dx="0" dy="6" stdDeviation="10" flood-color="#1c3566" flood-opacity="0.4"/>
      </filter>
    </defs>
    <polygon points="600,29 40,993 1160,993" fill="var(--frame)" filter="url(#lift)"/>
    <polygon class="panel-top" points="600,63 342,507 858,507" fill="var(--panel)"/>
    <polygon class="panel-left" points="320,533 58,984 582,984" fill="var(--panel)"/>
    <polygon class="panel-right" points="880,533 618,984 1142,984" fill="var(--panel)"/>
    <polygon class="panel-centre" points="349,527 851,527 600,969" fill="var(--panel)"/>
    <polygon class="pointer" points="600,469 580,507 620,507" fill="var(--frame)"/>
    <polygon class="pointer" points="408,741 444,716 444,766" fill="var(--frame)"/>
    <polygon class="pointer" points="792,741 756,716 756,766" fill="var(--frame)"/>
  </svg>

  <div class="brand brand--rtn">
    <div class="brand-mark"></div>
    <div class="brand-name">RTN</div>
    <div class="brand-label">CONSEIL SANS PAPIER</div>
  </div>

  <div class="brand brand--vellamor">
    <div class="brand-mark"></div>
    <div class="brand-name">VELLAMOR</div>
    <div class="brand-label">PORTAIL VELLAMOR 2.0</div>
  </div>

  <div class="brand brand--troupelune">
    <div class="brand-mark"></div>
    <div class="brand-name">TroupéLune</div>
    <div class="brand-label">LICENCES POUR ANIMAUX</div>
  </div>

  <div class="brand brand--ombrevik">
    <div class="brand-mark"></div>
    <div class="brand-name">OMBREVIK</div>
    <div class="brand-label">PERMIS • CARTE • INVENTAIRE • TAXES</div>
  </div>
</body>
</html>
```